Tessaline Wellness Marketing Flyer

We are a new medical practice in the community and need a flyer to send to other medical offices to inform of our services. We just completed our logo with Draftmarketo and would like to incorporate that plus our marketing content into the flyer. Our medical practice has 2 divisions: (1)Mental Health/Psychiatry and (2) Migraine and Neurospasticity Management. Please see website for content and provider photos at www.TessaWellnet.com

Target Market(s)

Other Healthcare Professionals in the Community

Industry/Entity Type

Medical

Requirements
Must have
• Photos of all 5 healthcare providers, phone number, address, logo

```html
<!DOCTYPE html>
<html lang="en">
<head>
<meta charset="utf-8">
<title>Tessaline Wellness Flyer</title>
<link rel="stylesheet" href="https://fonts.googleapis.com/css2?family=Playfair+Display:wght@400;700&family=Source+Sans+3:wght@400;600;700&display=swap">
<style>
:root{
  --bg:#273039;
  --paper:#fbfaf3;
  --teal:#13a89e;
  --teal-bright:#1ccfc0;
  --green:#a5d63a;
  --ink:#1c1c1c;
  --body:#3a3a3a;
  --mint:#cdeee9;
}
*{margin:0;padding:0;box-sizing:border-box}
html,body{width:1200px;height:2646px;overflow:hidden;background:var(--bg)}
.canvas{position:relative;width:1200px;height:2646px}
.flyer{position:absolute;left:50px;top:611px;width:884px;height:1144px;background:var(--paper);overflow:hidden;transform:scale(1.2443);transform-origin:0 0;font-family:"Source Sans 3",Arial,sans-serif;color:var(--ink)}
.hero-photo{position:absolute;left:500px;top:120px;width:384px;height:803px;background:linear-gradient(160deg,#e9e4dc 0%,#cfc7bb 35%,#8a6a4a 55%,#d9a92c 75%,#6f665d 100%)}
.brand{position:absolute;left:105px;top:82px;width:320px;text-align:center}
.brand-dot{width:96px;height:96px;border-radius:50%;background:var(--teal);margin:0 auto 14px}
.brand-name{font-family:"Playfair Display",Georgia,serif;font-weight:400;color:var(--teal);font-size:38px;line-height:1.05;letter-spacing:3px;text-transform:uppercase}
.headline{position:absolute;left:93px;top:278px;font-family:"Playfair Display",Georgia,serif;font-weight:700;font-size:56px;line-height:51px;color:var(--teal)}
.headline .accent{color:var(--green)}
.services{position:absolute;left:93px;top:456px;font-weight:600;font-size:17px;line-height:19px}
.providers-title{position:absolute;left:93px;top:503px;font-family:"Playfair Display",Georgia,serif;font-size:36px;line-height:34px;color:var(--teal)}
.providers-text{position:absolute;left:93px;top:573px;width:380px;font-size:12.5px;line-height:15px;color:var(--body);letter-spacing:-.15px}
.provider{position:absolute;width:150px;text-align:center}
.portrait{width:104px;height:104px;border-radius:50%;margin:0 auto 6px;background:radial-gradient(circle at 50% 40%,#d8b49a 0 28%,#8c8f93 60%,#4e5a60 100%)}
.provider-name{font-family:"Playfair Display",Georgia,serif;font-size:15px;line-height:15px;color:var(--teal)}
.feature{position:absolute;top:955px;width:215px}
.feature svg{position:absolute;left:0;top:22px}
.feature h3{margin-left:56px;font-size:17px;line-height:17px;font-weight:600}
.feature p{margin-left:56px;margin-top:4px;font-size:12.5px;line-height:12.5px;color:var(--body)}
.feature.first h3,.feature.first p{margin-left:73px}
.contact-bar{position:absolute;left:0;top:1088px;width:884px;height:56px}
.contact{position:absolute;top:1100px;color:#fff;font-size:15px;display:flex;align-items:center;gap:6px}
.contact.phone{left:150px;font-weight:700;font-size:22px}
.contact.address{font-size:13px;line-height:13px}
</style>
</head>
<body>
<div class="canvas">
<div class="flyer">
  <div class="hero-photo" role="img" aria-label="Photo of a smiling woman in a yellow top looking at her phone on a sofa"></div>

  <div class="brand">
    <div class="brand-dot"></div>
    <div class="brand-name">Tessaline<br>Wellness</div>
  </div>

  <h1 class="headline">Helping Bodies<br>Helping Minds<br><span class="accent">Helping You</span></h1>
  <p class="services">Mental Health and Psychiatry Services<br>Migraine and Neurospasticity Intervention</p>

  <h2 class="providers-title">Meet Our Mental<br>Health Providers</h2>
  <p class="providers-text">Bringing comprehensive evaluation, medication management and psychotherapy to the full spectrum of mental health disorders including minor, moderate and major depression, bipolar disorder, ADD/ADHD, anxiety, schizophrenia, stress or grief reactions, and others.</p>

  <div class="provider" style="left:71px;top:641px"><div class="portrait" role="img" aria-label="Portrait of Milo Varrick"></div><div class="provider-name">Milo Varrick,<br>PMHNP - BC</div></div>
  <div class="provider" style="left:199px;top:641px"><div class="portrait" role="img" aria-label="Portrait of Dara Whitcombe"></div><div class="provider-name">Dara Whitcombe,<br>PMHNP - BC</div></div>
  <div class="provider" style="left:327px;top:641px"><div class="portrait" role="img" aria-label="Portrait of Owen Castrel"></div><div class="provider-name">Owen Castrel<br>PMHNP - BC</div></div>
  <div class="provider" style="left:136px;top:790px"><div class="portrait" role="img" aria-label="Portrait of Milo Varrick"></div><div class="provider-name">Milo Varrick,<br>PMHNP - BC</div></div>
  <div class="provider" style="left:264px;top:790px"><div class="portrait" role="img" aria-label="Portrait of Dr. Elias Brandvik"></div><div class="provider-name">Dr. Elias<br>Brandvik</div></div>

  <div class="feature first" style="left:130px">
    <svg width="64" height="40" viewBox="0 0 64 40" fill="none" stroke="#222" stroke-width="2"><path d="M6 18c0-9 11-15 25-15s25 6 25 15-11 15-25 15c-5 0-9-1-13-2l-11 5 3-8C7 25 6 22 6 18z"/><circle cx="23" cy="18" r="2.4"/><circle cx="31" cy="18" r="2.4"/><circle cx="39" cy="18" r="2.4"/></svg>
    <h3>New Patient<br>Evaluation</h3>
    <p>Consults provided for evaluation and manage-ment of patients with chronic migraines or neurospasticity challenges.</p>
  </div>
  <div class="feature" style="left:370px">
    <svg width="50" height="46" viewBox="0 0 50 46" fill="none" stroke="#222" stroke-width="2"><rect x="3" y="3" width="30" height="38"/><path d="M9 12h18M9 19h18M9 26h12"/><path d="M38 10h6v30l-3 5-3-5z"/></svg>
    <h3>New Patient<br>Evaluation</h3>
    <p>Botulinum toxin injections may be a recommended treatment option. If so, our office completes insurance pre-authorizations on your behalf.</p>
  </div>
  <div class="feature" style="left:600px">
    <svg width="46" height="40" viewBox="0 0 46 40" fill="none" stroke="#222" stroke-width="2"><rect x="2" y="6" width="42" height="32"/><path d="M2 14h42M12 2v8M34 2v8M2 22h42M2 30h42M12 14v24M22 14v24M32 14v24"/></svg>
    <h3>New Patient<br>Evaluation</h3>
    <p>Timely appointments following insurance approval are available to quickly get you on the road to relief.</p>
  </div>

  <svg class="contact-bar" viewBox="0 0 884 56" preserveAspectRatio="none">
    <defs>
      <linearGradient id="tealBand" x1="0" x2="1"><stop offset="0" stop-color="#1ccfc0"/><stop offset="1" stop-color="#13a89e"/></linearGradient>
    </defs>
    <path d="M115 56 C130 20 140 4 170 4 H340 C360 4 365 30 380 56 Z" fill="url(#tealBand)"/>
    <path d="M365 56 C380 24 388 4 410 4 H600 C620 4 628 30 640 56 Z" fill="var(--green)"/>
    <path d="M615 56 C630 24 640 4 665 4 H840 C860 4 870 40 884 56 Z" fill="url(#tealBand)"/>
  </svg>
  <div class="contact phone"><svg width="18" height="18" viewBox="0 0 24 24" fill="#fff"><path d="M6.6 10.8a15 15 0 0 0 6.6 6.6l2.2-2.2c.3-.3.7-.4 1-.2 1.1.4 2.3.6 3.6.6.6 0 1 .4 1 1V20c0 .6-.4 1-1 1A17 17 0 0 1 3 4c0-.6.4-1 1-1h3.5c.6 0 1 .4 1 1 0 1.3.2 2.5.6 3.6.1.3 0 .7-.2 1z"/></svg>208-555-0147</div>
  <div class="contact" style="left:395px;top:1105px"><svg width="14" height="14" viewBox="0 0 24 24" fill="none" stroke="#fff" stroke-width="2"><circle cx="12" cy="12" r="10"/><path d="M2 12h20M12 2c3 3 3 17 0 20M12 2c-3 3-3 17 0 20"/></svg>www.TessaWellnet.com</div>
  <div class="contact address" style="left:650px"><svg width="12" height="18" viewBox="0 0 12 18" fill="#fff"><path d="M6 0a6 6 0 0 0-6 6c0 4.5 6 12 6 12s6-7.5 6-12a6 6 0 0 0-6-6zm0 8.5A2.5 2.5 0 1 1 6 3.5a2.5 2.5 0 0 1 0 5z"/></svg><span>1187 N. Larkspur Ave, Suite B<br>Harrowfield, ID 83000</span></div>
</div>
</div>
</body>
</html>
```